Upmarket Dessert Lounge needs a Business Card Design

We are an upmarket dessert lounge needing a business card to match our image.

We want something that is simple yet beautiful, feminine, classy, sophisticated and elegant. We want it to stand out and don't mind if it is bold.

The design should include our logo and colours of red or maroon with gold highlights. We don't mind if black is used.

Marlow & Quince

Target Market(s)

For those who like to indulge or treat themselves and give in to their temptations on good quality desserts.

Industry/Entity Type

Business

Requirements
Must have
• Must include our logo and our name

Marlow & Quince

M & Q

```html
<!DOCTYPE html>
<html lang="en">
<head>
<meta charset="utf-8">
<title>Marlow &amp; Quince — Business Card</title>
<link rel="stylesheet" href="https://fonts.googleapis.com/css2?family=Open+Sans:wght@400;700&display=swap">
<style>
  :root {
    --backdrop: #e6e6e6;
    --card-white: #ffffff;
    --maroon: #7a1416;
    --ink: #333333;
    --peach-light: #fff3e6;
    --peach-mid: #fee2c0;
    --peach-deep: #fbc98c;
  }
  * { box-sizing: border-box; margin: 0; padding: 0; }
  html, body {
    width: 956px;
    height: 1200px;
    overflow: hidden;
    background: var(--backdrop);
    font-family: "Open Sans", Arial, sans-serif;
  }
  .canvas {
    position: relative;
    width: 956px;
    height: 1200px;
  }
  .card {
    position: absolute;
    width: 799px;
    height: 456px;
    border-radius: 26px;
    box-shadow: 0 3px 8px rgba(0, 0, 0, 0.25);
  }
  .card--front {
    left: 78px;
    top: 114px;
    background: var(--card-white);
  }
  .card--back {
    left: 73px;
    top: 632px;
    background: radial-gradient(ellipse at center, var(--peach-light) 0%, var(--peach-mid) 60%, var(--peach-deep) 100%);
  }
  .brand-name {
    position: absolute;
    left: 0;
    width: 100%;
    text-align: center;
    color: var(--maroon);
    font-weight: 400;
    white-space: nowrap;
  }
  .card--front .brand-name {
    top: 106px;
    font-size: 46px;
    line-height: 50px;
    letter-spacing: 2px;
  }
  .card--back .brand-name {
    top: 168px;
    font-size: 112px;
    line-height: 120px;
    letter-spacing: 4px;
  }
  .contact {
    position: absolute;
    left: 0;
    top: 266px;
    width: 100%;
    text-align: center;
    color: var(--ink);
    font-size: 22px;
    line-height: 40px;
    white-space: nowrap;
  }
  .contact__person {
    font-size: 23px;
    margin-bottom: 10px;
  }
  .contact__person strong,
  .contact__label { font-weight: 700; }
  .contact__sep { margin: 0 9px; }
</style>
</head>
<body>
<main class="canvas">
  <section class="card card--front">
    <div class="brand-name">Marlow &amp; Quince</div>
    <div class="contact">
      <p class="contact__person"><strong>Your Name -</strong> Designation</p>
      <p><span class="contact__label">p</span> : 123-456-7890<span class="contact__sep">|</span><span class="contact__label">c</span> : 123-456-7890<span class="contact__sep">|</span><span class="contact__label">f</span> : 123-456-7890</p>
      <p><span class="contact__label">e</span> : name@yourwebsite.com<span class="contact__sep">|</span><span class="contact__label">w</span> : www.marlowandquince.com</p>
      <p>0000, Street Name, City Name, Country Code.</p>
    </div>
  </section>
  <section class="card card--back">
    <div class="brand-name">M &amp; Q</div>
  </section>
</main>
</body>
</html>
```